Brightfen Business Card Redesign & Logo Update

We need to update our business cards to something more modern and fresh. Brightfen can provide the current color schemes and old design examples, but welcome creativity in helping us with this redesign. PLEASE NOTE that we no longer utilize the "tree" and/or "leaf" imagery in our branding. If able would apprecaite an update on the quality of our "words only" logo in Ai. / PNG formats too.

Target Market(s)

Investors, landowners, corporate partners, contractors

Industry/Entity Type

Environmental Restoration & Conservation

Contact Information for Business Card

Logo, persons name, title, mailing address, phone and email, website url

Font styles to use
Other font styles liked:
• Merriweather

Requirements
Nice to have
• Logo, persons name, title, mailing address, phone and email, website url, but open to ideams
Should not have
• No all back backgrounds

```html
<!DOCTYPE html>
<html lang="en">
<head>
<meta charset="utf-8">
<title>Brightfen Business Card</title>
<link rel="stylesheet" href="https://fonts.googleapis.com/css2?family=Oswald:wght@600;700&family=Open+Sans:wght@400;600;700&display=swap">
<style>
  :root {
    --stage: #3a3a3a;
    --card: #1b1b1b;
    --card-deep: #121212;
    --orange: #f07f1c;
    --green: #1f8a44;
    --white: #f2f2f2;
  }
  * { box-sizing: border-box; margin: 0; padding: 0; }
  html, body { width: 1200px; height: 801px; overflow: hidden; }
  body {
    background: var(--stage);
    font-family: "Open Sans", sans-serif;
    position: relative;
  }
  .card {
    position: absolute;
    width: 520px;
    height: 298px;
    border-radius: 18px;
    border: 1.5px solid var(--orange);
    background: var(--card);
    overflow: hidden;
  }
  .card--front { left: 50px; top: 252px; }
  .card--back { left: 630px; top: 252px; }

  .logo {
    position: absolute;
    right: 40px;
    top: 38px;
    text-align: right;
  }
  .logo__name {
    font-family: "Oswald", sans-serif;
    font-weight: 700;
    font-size: 50px;
    line-height: 1;
    letter-spacing: 1px;
    color: var(--orange);
  }
  .logo__tagline {
    font-family: "Oswald", sans-serif;
    font-weight: 600;
    font-size: 11.5px;
    letter-spacing: 0.4px;
    color: var(--white);
    margin-top: 3px;
  }
  .contact {
    position: absolute;
    right: 40px;
    top: 140px;
    width: 220px;
    color: var(--white);
    font-size: 12.5px;
    line-height: 1.45;
  }
  .contact__address { margin-bottom: 14px; }
  .contact__row { display: flex; align-items: center; gap: 7px; }
  .contact__icon { width: 11px; height: 11px; flex: none; }

  .person {
    position: absolute;
    left: 40px;
    bottom: 46px;
  }
  .person__name {
    font-weight: 700;
    font-size: 21px;
    letter-spacing: 0.5px;
    color: var(--orange);
    text-transform: uppercase;
  }
  .person__title {
    font-size: 15px;
    color: var(--white);
  }
  .edge-tab {
    position: absolute;
    left: -2px;
    bottom: 44px;
    width: 14px;
    height: 26px;
    border-radius: 0 8px 8px 0;
    background: var(--orange);
  }

  .back-texture {
    position: absolute;
    inset: 0;
    background: linear-gradient(120deg, var(--card-deep) 0%, #1e1e1e 45%, #2c2c2c 100%);
  }
  .back-logo {
    position: absolute;
    right: 40px;
    bottom: 40px;
    font-family: "Oswald", sans-serif;
    font-weight: 700;
    font-size: 32px;
    letter-spacing: 1px;
    color: var(--orange);
  }
</style>
</head>
<body>
  <section class="card card--front">
    <div class="logo">
      <div class="logo__name">BRIGHTFEN</div>
      <div class="logo__tagline">ENVIRONMENTAL CREDIT COMPANY</div>
    </div>
    <div class="contact">
      <p class="contact__address">1840 Crestline Harbor<br>Bayview CA 92600</p>
      <p class="contact__row">
        <svg class="contact__icon" viewBox="0 0 12 12"><circle cx="6" cy="6" r="6" fill="var(--green)"/><path d="M3.6 3.2l1.2-.3.6 1.5-.8.6a4.5 4.5 0 0 0 2.4 2.4l.6-.8 1.5.6-.3 1.2C6 8.6 3.4 6 3.6 3.2z" fill="var(--card)"/></svg>
        555-013-2847
      </p>
      <p class="contact__row">
        <svg class="contact__icon" viewBox="0 0 12 12"><rect x="0.5" y="2" width="11" height="8" rx="1" fill="var(--green)"/><path d="M1 2.6l5 3.6 5-3.6" stroke="var(--card)" fill="none"/></svg>
        dcorwell@brightfen.com
      </p>
      <p class="contact__row">
        <svg class="contact__icon" viewBox="0 0 12 12"><circle cx="6" cy="6" r="6" fill="var(--green)"/><path d="M1 6h10M6 0.5c-2.5 3-2.5 8 0 11M6 0.5c2.5 3 2.5 8 0 11" stroke="var(--card)" stroke-width="0.8" fill="none"/></svg>
        www.brightfen.com
      </p>
    </div>
    <div class="person">
      <p class="person__name">Dan Corwell</p>
      <p class="person__title">President</p>
    </div>
    <span class="edge-tab"></span>
  </section>

  <section class="card card--back">
    <div class="back-texture" role="img" aria-label="Dark repeating brand-name texture across the card back"></div>
    <div class="back-logo">BRIGHTFEN</div>
  </section>
</body>
</html>
```